Website design for a hair building fibre

Hi I’m needing a website made for both men and women to purchase the product is a hair building fibre that you apply to thinning hair to make your hair look really thick I’ll need the website to be easy to use professional and also very classy I will need it to work with lumen split tok fund and credit cards I’ll need to have the CEO words and everything ready so I can sell I don’t have photos that I want to put on there so I’ll need a website designer to assist me in having the beautiful photos on there I know very little about websites so I need someone to be able to do it all for me

I can only provide photos of the colours of the products
I believe there will be 8 colours to sell as well
I’ve uploaded a photo of the logo I’d really like it if the website designer can check other competitors website so my website does not look like theres, I don’t want my website to look like a copied website of the competitors I’m located in Australia.
I’m also looking for someone who can open up a Palvista and Glimmerly page and then can unload photos on them ready for consumers to view and buy.

```html
<!DOCTYPE html>
<html lang="en">
<head>
<meta charset="utf-8">
<title>Strandfull — Hair Building Fibre</title>
<link rel="stylesheet" href="https://fonts.googleapis.com/css2?family=Montserrat:wght@300;400;500;600;700&family=Open+Sans:ital,wght@0,400;0,600;1,400&display=swap">
<style>
:root{
  --navy:#111a26;
  --sky:#6fd3f5;
  --sky-soft:#c7eaf5;
  --band:#76bfe0;
  --ink:#1a1f2b;
  --grey:#7c7c7c;
  --line:#d7d7d7;
  --red:#e3173e;
}
*{margin:0;padding:0;box-sizing:border-box}
html,body{width:1200px;height:3891px;overflow:hidden}
body{position:relative;font-family:"Open Sans",sans-serif;color:var(--ink);background:#fff}
.abs{position:absolute}
.mont{font-family:"Montserrat",sans-serif}

/* header */
.site-header{left:0;top:0;width:1200px;height:112px;background:var(--navy)}
.brand{font-family:"Montserrat",sans-serif;font-weight:300;color:var(--sky);letter-spacing:2px}
.site-header .brand{left:145px;top:24px;font-size:42px;line-height:44px}
.site-header .tag{left:146px;top:74px;font-size:15px;letter-spacing:4px;color:#c9d3dc;font-family:"Montserrat",sans-serif;font-weight:300}
.search{left:762px;top:14px;width:196px;height:37px;background:#fff;font-size:12px;padding:11px 20px;color:#555}
.search-btn{left:958px;top:14px;width:39px;height:37px;background:var(--sky)}
.nav{left:505px;top:74px;display:flex;gap:40px;font-family:"Montserrat",sans-serif;font-size:16px;color:#fff;font-weight:500}

/* hero */
.hero{left:0;top:112px;width:1200px;height:506px;background:linear-gradient(90deg,#cfeef8 0%,#bfe6f3 45%,#9fc6d6 70%,#7da6b8 100%)}
.hero-photo{left:600px;top:112px;width:600px;height:506px;background:linear-gradient(90deg,rgba(191,230,243,0) 0%,#8fb5c5 35%,#6b8f9f 70%,#a9c3cd 100%)}
.hero .brand{left:254px;top:96px;font-size:84px;line-height:86px;letter-spacing:3px}
.hero .tag{left:256px;top:184px;font-size:28px;letter-spacing:7px;color:#8fd4ea;font-family:"Montserrat",sans-serif;font-weight:300}
.hero .lead{left:256px;top:236px;font-family:"Montserrat",sans-serif;font-weight:600;font-size:19px;color:#1d2633}
.btn{background:var(--sky);color:#0f1822;font-family:"Montserrat",sans-serif;font-weight:600;text-align:center;border-radius:40px}
.hero .btn{left:256px;top:300px;width:164px;height:60px;line-height:60px;font-size:16px}
.dots{left:258px;top:422px;display:flex;gap:11px}
.dots i{width:13px;height:13px;border-radius:50%;background:#b5b5b5}
.dots i.on{background:var(--sky)}

/* sections */
.sec-title{left:0;width:1200px;text-align:center;font-family:"Montserrat",sans-serif;font-weight:700;font-size:42px;color:var(--ink)}
.rule{left:571px;width:58px;height:5px;background:var(--sky)}

/* products */
.card{width:213px;height:258px;border:2px solid var(--line);background:#fff}
.card.active{background:var(--sky-soft);border:4px solid #d6f0f8}
.bottle{left:70px;top:18px;width:70px;height:230px;border-radius:10px 10px 0 0;background:linear-gradient(90deg,#1c1c1c,#5a5a5a 35%,#2a2a2a 70%,#111)}
.new{right:12px;top:14px;background:var(--red);color:#fff;font-family:"Montserrat",sans-serif;font-weight:700;font-size:12px;padding:3px 5px}
.card .btn{left:58px;top:194px;width:96px;height:34px;line-height:34px;font-size:12px}
.pname{width:213px;text-align:center;font-family:"Montserrat",sans-serif;font-weight:600;font-size:17px}
.swatches{width:213px;display:flex;justify-content:center;gap:6px}
.swatches i{width:17px;height:17px;border-radius:50%}
.price{width:213px;text-align:center;font-family:"Montserrat",sans-serif;font-weight:600;font-size:16px;color:var(--sky)}

/* about */
.about-bg{left:0;top:1713px;width:600px;height:448px;background:linear-gradient(90deg,#dbe8ef,#eef4f8 70%,#f6f9fb)}
.about-photo{left:600px;top:1713px;width:600px;height:448px;background:linear-gradient(90deg,#9a5a22,#c46a2a 35%,#d98a3e 60%,#b67a43 100%)}
.about-title{left:133px;top:1808px;font-family:"Montserrat",sans-serif;font-weight:700;font-size:42px}
.about-copy{left:145px;top:1870px;width:400px;font-size:13px;line-height:25.5px;color:#555}
.about .btn{left:145px;top:1998px;width:164px;height:60px;line-height:60px;font-size:16px}
.play{left:874px;top:1914px;width:48px;height:48px;border-radius:50%;background:#fff}

/* blog */
.blog{left:144px;top:2362px;width:912px;height:490px;border:1px solid var(--line)}
.blog-cell{width:304px;height:245px}
.blog-text{text-align:center;padding:24px 22px}
.blog-text h3{font-family:"Montserrat",sans-serif;font-weight:400;font-size:16px;line-height:23px;margin-bottom:12px}
.blog-text p{font-size:12px;line-height:23px;color:var(--grey);margin-bottom:20px}
.blog-text .btn{display:inline-block;width:126px;height:44px;line-height:44px;font-size:12px}

/* reviews */
.reviews{left:0;top:2956px;width:1200px;height:415px;background:var(--band)}
.reviews .sec-title{top:88px;color:#fff}
.review{width:300px}
.avatar{width:68px;height:68px;border-radius:50%;border:3px solid #fff}
.quote{left:82px;top:0;width:220px;font-size:11px;line-height:21px;font-style:italic;color:#fff}
.rname{left:82px;top:92px;font-family:"Montserrat",sans-serif;font-size:8.5px;color:#fff}
.rrole{left:82px;top:106px;font-size:8.5px;font-style:italic;color:#fff}
.stars{left:82px;top:136px}
.arrow{width:34px;height:34px;border-radius:50%;border:2px solid #fff}

/* mailing */
.mailing{left:0;top:3371px;width:1200px;height:107px;background:var(--navy)}
.mailing h2{left:144px;top:36px;font-family:"Montserrat",sans-serif;font-weight:400;font-size:30px;color:#fff}
.email{left:535px;top:36px;width:384px;height:37px;background:#fff;font-size:13px;padding:10px 20px;color:#444}
.signup{left:928px;top:36px;width:128px;height:37px;background:var(--sky);color:#fff;font-family:"Montserrat",sans-serif;font-weight:600;font-size:15px;text-align:center;line-height:37px}

/* footer */
.footer{left:0;top:3478px;width:1200px;height:413px;background:linear-gradient(160deg,#fafafa,#f6f0f4 40%,#eef4fa 80%,#fbf3ee)}
.fcol h4{font-family:"Montserrat",sans-serif;font-weight:600;font-size:15px;margin-bottom:10px}
.fcol li{list-style:none;font-size:13px;line-height:23px;color:#666}
.contact-row{display:flex;gap:12px;font-size:13px;line-height:18px;color:#666;margin-bottom:14px}
.social{display:flex;gap:6px}
.social i{width:28px;height:28px;border-radius:50%}
.cards{left:145px;top:3726px;display:flex;gap:8px}
.cards i{width:33px;height:21px;border-radius:2px}
.copy{right:144px;top:3727px;font-size:13px;color:#555}
.divider{left:145px;top:3704px;width:911px;height:1px;background:#ddd}
.disclaimer{left:190px;top:3784px;width:820px;text-align:center;font-size:12.5px;line-height:23px;color:#333;font-style:italic}
.disclaimer b{font-style:normal}
</style>
</head>
<body>

<header class="site-header abs">
  <div class="brand abs">Strandfull</div>
  <div class="tag abs">HAIR BUILDING FIBRE</div>
  <div class="search abs">Search</div>
  <div class="search-btn abs">
    <svg width="39" height="37" viewBox="0 0 39 37"><circle cx="18" cy="17" r="5" fill="none" stroke="#fff" stroke-width="2"/><line x1="22" y1="21" x2="25" y2="24" stroke="#fff" stroke-width="2"/></svg>
  </div>
  <svg class="abs" style="left:1012px;top:16px" width="40" height="34" viewBox="0 0 40 34" fill="none" stroke="#fff" stroke-width="2"><path d="M2 6h6l5 16h18l4-12H10"/><circle cx="15" cy="28" r="2.5"/><circle cx="28" cy="28" r="2.5"/><circle cx="31" cy="8" r="6"/><path d="M31 5v6M28 8h6"/></svg>
  <nav class="nav abs"><span>HOME</span><span>ABOUT</span><span>PRODUCTS</span><span>NEWS</span><span>BLOG</span><span>CONTACT</span></nav>
</header>

<section class="hero abs">
  <div class="abs" role="img" aria-label="Soft outline of a woman's profile with flowing hair" style="left:0;top:0;width:420px;height:506px;background:linear-gradient(135deg,rgba(160,210,230,.5),rgba(207,238,248,0))"></div>
  <div class="brand abs">Strandfull</div>
  <div class="tag abs">HAIR BUILDING FIBRE</div>
  <div class="lead abs">Lorem ipsum doloametconseadipiscing elit</div>
  <div class="btn abs">SHOP NOW</div>
  <div class="dots abs"><i></i><i class="on"></i><i></i></div>
</section>
<div class="hero-photo abs" role="img" aria-label="Blue-toned portrait of a woman with long wavy hair"></div>

<h2 class="sec-title abs" style="top:718px">FEATURED PRODUCTS</h2>
<div class="rule abs" style="top:778px"></div>

<!-- product grid -->
<div class="card abs" style="left:142px;top:845px"><div class="bottle abs" role="img" aria-label="Black fibre bottle"></div><span class="new abs">NEW</span></div>
<div class="card active abs" style="left:374px;top:843px"><div class="bottle abs" role="img" aria-label="Grey fibre bottle"></div><span class="new abs">NEW</span><div class="btn abs">SHOP NOW</div></div>
<div class="card abs" style="left:610px;top:845px"><div class="bottle abs" role="img" aria-label="Brown fibre bottle"></div><span class="new abs">NEW</span></div>
<div class="card abs" style="left:845px;top:845px"><div class="bottle abs" role="img" aria-label="Orange fibre bottle"></div><span class="new abs">NEW</span></div>

<div class="card abs" style="left:142px;top:1250px"><div class="bottle abs" role="img" aria-label="Violet fibre bottle"></div><span class="new abs">NEW</span></div>
<div class="card abs" style="left:376px;top:1250px"><div class="bottle abs" role="img" aria-label="Grey fibre bottle"></div><span class="new abs">NEW</span></div>
<div class="card abs" style="left:610px;top:1250px"><div class="bottle abs" role="img" aria-label="Black fibre bottle"></div><span class="new abs">NEW</span></div>
<div class="card abs" style="left:845px;top:1250px"><div class="bottle abs" role="img" aria-label="Green fibre bottle"></div><span class="new abs">NEW</span></div>

<!-- product info rows -->
<div class="abs" style="left:142px;top:1128px">
  <div class="pname">PRODUCT NAME</div>
</div>
<div class="abs" style="left:376px;top:1128px"><div class="pname">PRODUCT NAME</div></div>
<div class="abs" style="left:610px;top:1128px"><div class="pname">PRODUCT NAME</div></div>
<div class="abs" style="left:845px;top:1128px"><div class="pname">PRODUCT NAME</div></div>
<div class="abs" style="left:142px;top:1533px"><div class="pname">PRODUCT NAME</div></div>
<div class="abs" style="left:376px;top:1533px"><div class="pname">PRODUCT NAME</div></div>
<div class="abs" style="left:610px;top:1533px"><div class="pname">PRODUCT NAME</div></div>
<div class="abs" style="left:845px;top:1533px"><div class="pname">PRODUCT NAME</div></div>

<div class="swatches abs" style="left:142px;top:1167px"><i style="background:#4a4a4a"></i><i style="background:#6b2a0e"></i><i style="background:#ecd2ae"></i><i style="background:#d87c46"></i><i style="background:#8fbfa8"></i><i style="background:#4a0f4f"></i><i style="background:#9a4a1c"></i><i style="background:#111"></i></div>
<div class="swatches abs" style="left:376px;top:1167px"><i style="background:#4a4a4a"></i><i style="background:#6b2a0e"></i><i style="background:#ecd2ae"></i><i style="background:#d87c46"></i><i style="background:#8fbfa8"></i><i style="background:#4a0f4f"></i><i style="background:#9a4a1c"></i><i style="background:#111"></i></div>
<div class="swatches abs" style="left:610px;top:1167px"><i style="background:#4a4a4a"></i><i style="background:#6b2a0e"></i><i style="background:#ecd2ae"></i><i style="background:#d87c46"></i><i style="background:#8fbfa8"></i><i style="background:#4a0f4f"></i><i style="background:#9a4a1c"></i><i style="background:#111"></i></div>
<div class="swatches abs" style="left:845px;top:1167px"><i style="background:#4a4a4a"></i><i style="background:#6b2a0e"></i><i style="background:#ecd2ae"></i><i style="background:#d87c46"></i><i style="background:#8fbfa8"></i><i style="background:#4a0f4f"></i><i style="background:#9a4a1c"></i><i style="background:#111"></i></div>
<div class="swatches abs" style="left:142px;top:1572px"><i style="background:#4a4a4a"></i><i style="background:#6b2a0e"></i><i style="background:#ecd2ae"></i><i style="background:#d87c46"></i><i style="background:#8fbfa8"></i><i style="background:#4a0f4f"></i><i style="background:#9a4a1c"></i><i style="background:#111"></i></div>
<div class="swatches abs" style="left:376px;top:1572px"><i style="background:#4a4a4a"></i><i style="background:#6b2a0e"></i><i style="background:#ecd2ae"></i><i style="background:#d87c46"></i><i style="background:#8fbfa8"></i><i style="background:#4a0f4f"></i><i style="background:#9a4a1c"></i><i style="background:#111"></i></div>
<div class="swatches abs" style="left:610px;top:1572px"><i style="background:#4a4a4a"></i><i style="background:#6b2a0e"></i><i style="background:#ecd2ae"></i><i style="background:#d87c46"></i><i style="background:#8fbfa8"></i><i style="background:#4a0f4f"></i><i style="background:#9a4a1c"></i><i style="background:#111"></i></div>
<div class="swatches abs" style="left:845px;top:1572px"><i style="background:#4a4a4a"></i><i style="background:#6b2a0e"></i><i style="background:#ecd2ae"></i><i style="background:#d87c46"></i><i style="background:#8fbfa8"></i><i style="background:#4a0f4f"></i><i style="background:#9a4a1c"></i><i style="background:#111"></i></div>

<div class="price abs" style="left:142px;top:1202px">$56.67</div>
<div class="price abs" style="left:376px;top:1202px">$56.67</div>
<div class="price abs" style="left:610px;top:1202px">$56.67</div>
<div class="price abs" style="left:845px;top:1202px">$56.67</div>
<div class="price abs" style="left:142px;top:1607px">$56.67</div>
<div class="price abs" style="left:376px;top:1607px">$56.67</div>
<div class="price abs" style="left:610px;top:1607px">$56.67</div>
<div class="price abs" style="left:845px;top:1607px">$56.67</div>

<!-- about -->
<section class="about">
  <div class="about-bg abs" role="img" aria-label="Faded harbour city skyline"></div>
  <div class="about-photo abs" role="img" aria-label="Woman with curly hair shown in several colour tones, video still"></div>
  <div class="play abs"><svg width="48" height="48" viewBox="0 0 48 48"><path d="M19 14l16 10-16 10z" fill="var(--sky)"/></svg></div>
  <h2 class="about-title abs">ABOUT</h2>
  <p class="about-copy abs">Lorem ipsum dolor sit amet, consectetur adipiscinged do eiusmod tempor incididunt ut labore et dolore magna aliqua.uis suspendisse ultrices gravisus commodo viverra maecenas accumsan lacus vel facili viverra maecenas accumsan lacsis.</p>
  <div class="btn abs">SHOP NOW</div>
</section>

<!-- blog -->
<h2 class="sec-title abs" style="top:2254px">FROM THE BLOG</h2>
<div class="blog abs">
  <div class="blog-cell abs" style="left:0;top:0;background:linear-gradient(90deg,#e39a82 0 54%,#cfcfd3 54%)" role="img" aria-label="Two smiling women with red and violet hair"></div>
  <div class="blog-cell blog-text abs" style="left:304px;top:0">
    <h3>NEMO ENIM IPSAM VOLUPTATEM QUIA VOLUPTAS SIT</h3>
    <p>At vero eos et accusamus et iusto odio dignissiducimumos ducimus qui blanditiis pducimuducimuraesentiu</p>
    <span class="btn">READ MORE</span>
  </div>
  <div class="blog-cell abs" style="left:608px;top:0;background:linear-gradient(135deg,#d8c3aa,#b89878)" role="img" aria-label="Woman with voluminous purple curls"></div>
  <div class="blog-cell blog-text abs" style="left:0;top:245px">
    <h3>NEMO ENIM IPSAM VOLUPTATEM QUIA VOLUPTAS SIT</h3>
    <p>At vero eos et accusamus et iusto odio dignissiducimumos ducimus qui blanditiis pducimuducimuraesentiu</p>
    <span class="btn">READ MORE</span>
  </div>
  <div class="blog-cell abs" style="left:304px;top:245px;background:linear-gradient(135deg,#e9eaee,#c9ccd4)" role="img" aria-label="Woman with long platinum blonde hair"></div>
  <div class="blog-cell blog-text abs" style="left:608px;top:245px">
    <h3>NEMO ENIM IPSAM VOLUPTATEM QUIA VOLUPTAS SIT</h3>
    <p>At vero eos et accusamus et iusto odio dignissiducimumos ducimus qui blanditiis pducimuducimuraesentiu</p>
    <span class="btn">READ MORE</span>
  </div>
</div>

<!-- reviews -->
<section class="reviews abs">
  <h2 class="sec-title abs">CUSTOMER REVIEWS</h2>
  <div class="arrow abs" style="left:67px;top:251px"><svg width="30" height="30" viewBox="0 0 30 30"><path d="M17 9l-6 6 6 6" fill="none" stroke="#fff" stroke-width="2"/></svg></div>
  <div class="arrow abs" style="left:1099px;top:251px"><svg width="30" height="30" viewBox="0 0 30 30"><path d="M13 9l6 6-6 6" fill="none" stroke="#fff" stroke-width="2"/></svg></div>

  <div class="review abs" style="left:130px;top:180px;height:160px">
    <div class="avatar abs" style="background:#d9b8a5" role="img" aria-label="Customer portrait"></div>
    <p class="quote abs">“ At vero eos et accusamus et iustodio dignissimos ducimus qui blanditiipraesnt ium voluptatum deleniti atq.</p>
    <div class="rname abs">MARLA QUINN</div>
    <div class="rrole abs">Financial Services Professional</div>
    <svg class="stars abs" width="100" height="16" viewBox="0 0 100 16"><g fill="#ffd23a"><path id="st" d="M8 1l2 5h5l-4 3 2 5-5-3-5 3 2-5-4-3h5z"/><use href="#st" x="20"/><use href="#st" x="40"/><use href="#st" x="60"/></g><use href="#st" x="80" fill="none" stroke="#ffd23a"/></svg>
  </div>
  <div class="review abs" style="left:455px;top:180px;height:160px">
    <div class="avatar abs" style="background:#c8c8c8" role="img" aria-label="Customer portrait"></div>
    <p class="quote abs">“ At vero eos et accusamus et iustodio dignissimos ducimus qui blanditiipraesnt ium voluptatum deleniti atq.</p>
    <div class="rname abs">TAVIN R. OSGOOD</div>
    <div class="rrole abs">National Urban Fellow at the Riverton</div>
    <svg class="stars abs" width="100" height="16" viewBox="0 0 100 16"><g fill="#ffd23a"><use href="#st"/><use href="#st" x="20"/><use href="#st" x="40"/><use href="#st" x="60"/><use href="#st" x="80" opacity=".6"/></g></svg>
  </div>
  <div class="review abs" style="left:778px;top:180px;height:160px">
    <div class="avatar abs" style="background:#d6c9bf" role="img" aria-label="Customer portrait"></div>
    <p class="quote abs">“ At vero eos et accusamus et iustodio dignissimos ducimus qui blanditiipraesnt ium voluptatum deleniti atq.</p>
    <div class="rname abs">ILSA RENWICK</div>
    <div class="rrole abs">Creative Strategist | Entrepreneur &amp; Upcoming</div>
    <svg class="stars abs" width="100" height="16" viewBox="0 0 100 16"><g fill="#ffd23a"><use href="#st"/><use href="#st" x="20"/><use href="#st" x="40"/><use href="#st" x="60"/></g><use href="#st" x="80" fill="none" stroke="#ffd23a"/></svg>
  </div>
</section>

<!-- mailing list -->
<section class="mailing abs">
  <h2 class="abs">JOIN OUR MAILING LIST</h2>
  <div class="email abs">Enter Email</div>
  <div class="signup abs">SIGN UP</div>
  <svg class="abs" style="left:1111px;top:33px" width="42" height="42" viewBox="0 0 42 42"><circle cx="21" cy="21" r="19" fill="none" stroke="var(--sky)" stroke-width="2.5"/><path d="M21 31V12M13 19l8-8 8 8" fill="none" stroke="var(--sky)" stroke-width="3"/></svg>
</section>

<!-- footer -->
<footer class="footer abs">
  <div class="fcol abs" style="left:145px;top:58px;width:230px">
    <h4>CONTACT US</h4>
    <div class="contact-row"><svg width="20" height="18" viewBox="0 0 20 18"><path d="M10 1l9 8h-3v8h-4v-5H8v5H4V9H1z" fill="#5aa9d6"/></svg><span>134,Sed ut perspiciatis unde omnis iste natus erro..</span></div>
    <div class="contact-row"><svg width="20" height="18" viewBox="0 0 20 18"><path d="M4 2l4 4-2 2a10 10 0 005 5l2-2 4 4-3 2C8 17 2 10 2 5z" fill="#5aa9d6"/></svg><span>Call us : +1 555 014 2290</span></div>
    <div class="contact-row"><svg width="20" height="18" viewBox="0 0 20 18"><rect x="1" y="3" width="18" height="12" fill="#5aa9d6"/><path d="M1 3l9 7 9-7" fill="none" stroke="#fff" stroke-width="1.5"/></svg><span>info@strandfull.com</span></div>
  </div>
  <div class="fcol abs" style="left:409px;top:58px">
    <h4>ACCOUNTS &amp; ORDERS</h4>
    <ul><li>Gift Certificates</li><li>Wishlist</li><li>Login or Sign up</li><li>Shipping &amp; Returns</li><li>Sitemap</li></ul>
  </div>
  <div class="fcol abs" style="left:651px;top:58px">
    <h4>QUICK LINKS</h4>
    <ul><li>Why Choose us</li><li>Shipping &amp; returns</li><li>Contact us</li><li>Blog</li></ul>
  </div>
  <div class="fcol abs" style="left:858px;top:58px">
    <h4>RECENT BLOG POSTS</h4>
    <ul><li>Your first blog Post!</li></ul>
    <h4 style="margin-top:18px">CONNECT WITH US</h4>
    <div class="social"><i style="background:#3b5998"></i><i style="background:#1da1f2"></i><i style="background:#e0312b"></i><i style="background:#b58a5a"></i></div>
  </div>
</footer>
<div class="divider abs"></div>
<div class="cards abs"><i style="background:#e9552b"></i><i style="background:#f2b21b"></i><i style="background:#2f7cc0"></i><i style="background:#d8d8d8"></i></div>
<div class="copy abs">© copyright 2022 Strandfull.All Rights Reserved &nbsp;|&nbsp; Privacy policy</div>
<p class="disclaimer abs"><b>Disclaimer :</b> Lorem ipsum carrots, enhanced undergraduate developer, but they do occaecat time and vitality, such as labor and obesity. Over the years come nostrud exercis school district work unless they aliquip advantage fromomework if cupidatat consumer to find pleasure wants to look for the pleasure. d information as quis nostrum exercitationem be a football cillum he shuns pain,</p>

</body>
</html>
```